Veldmark Supplies Business Card

Professional business card that stand out to our potential customers. Front and back with clean modern design

Industry/Entity Type

Oil and gas

Contact Information for Business Card

Name, address, website , office phone and cell number

Requirements
Must have
• Editable files for each employee

```html
<!DOCTYPE html>
<html lang="en">
<head>
<meta charset="utf-8">
<title>Veldmark Supplies Business Card</title>
<link rel="stylesheet" href="https://fonts.googleapis.com/css2?family=Montserrat:wght@300;400;600;700;800&display=swap">
<style>
  :root {
    --red: #e8232b;
    --blue: #14aed6;
    --black: #0b0b0b;
    --charcoal: #2a2a2a;
    --white: #ffffff;
    --ink: #1e1e1e;
    --backdrop: #e9e7e3;
  }
  * { margin: 0; padding: 0; box-sizing: border-box; }
  html, body {
    width: 1200px; height: 1014px; overflow: hidden;
    background: var(--backdrop);
    font-family: "Montserrat", Arial, sans-serif;
  }
  .canvas { position: relative; width: 1200px; height: 1014px; }
  .card {
    position: absolute; left: 200px; width: 800px; height: 457px;
    background: var(--white); overflow: hidden;
    box-shadow: 0 6px 18px rgba(0,0,0,0.18);
  }
  .card--front { top: 40px; }
  .card--back { top: 517px; }

  /* front */
  .front__brand {
    height: 210px; display: flex; align-items: center; padding-left: 70px; gap: 18px;
  }
  .brand-square { width: 54px; height: 54px; background: var(--blue); }
  .brand-name {
    font-weight: 800; font-size: 48px; color: var(--red);
    text-transform: uppercase; letter-spacing: 1px;
  }
  .front__details {
    position: absolute; left: 0; right: 0; bottom: 0; height: 247px;
    background: linear-gradient(120deg, var(--charcoal) 0%, var(--black) 45%, var(--black) 100%);
    display: flex; justify-content: space-between; align-items: center;
    padding: 0 60px 0 70px;
  }
  .person__name { font-weight: 700; font-size: 34px; }
  .person__first { color: var(--red); }
  .person__last { color: var(--blue); }
  .person__title { color: var(--white); font-weight: 300; font-size: 22px; margin-top: 8px; }
  .contact-list { list-style: none; }
  .contact-list li {
    display: flex; align-items: center; gap: 14px;
    color: var(--white); font-weight: 300; font-size: 19px; line-height: 1.85;
  }
  .contact-list svg { width: 20px; height: 20px; flex: none; }

  /* back */
  .back__brand {
    position: absolute; top: 120px; left: 0; right: 0;
    display: flex; justify-content: center; align-items: center; gap: 18px;
  }
  .back__brand .brand-square { width: 64px; height: 64px; }
  .back__brand .brand-name { font-size: 54px; }
  .back__info { position: absolute; left: 70px; bottom: 60px; }
  .back__web { font-weight: 700; font-size: 26px; }
  .back__web .web-red { color: var(--red); }
  .back__web .web-blue { color: var(--blue); }
  .back__address { font-weight: 400; font-size: 21px; color: var(--ink); margin-top: 8px; }
</style>
</head>
<body>
<main class="canvas">
  <section class="card card--front">
    <div class="front__brand">
      <span class="brand-square"></span>
      <span class="brand-name">Veldmark Supplies</span>
    </div>
    <div class="front__details">
      <div class="person">
        <p class="person__name"><span class="person__first">Dale</span> <span class="person__last">Hartwell</span></p>
        <p class="person__title">Manager &amp; Owner</p>
      </div>
      <ul class="contact-list">
        <li>
          <svg viewBox="0 0 24 24" fill="none" stroke="#14aed6" stroke-width="2"><path d="M5 3h4l2 5-2.5 1.5a11 11 0 0 0 6 6L16 13l5 2v4a2 2 0 0 1-2 2A16 16 0 0 1 3 5a2 2 0 0 1 2-2z"/></svg>
          (555) 210-0148
        </li>
        <li>
          <svg viewBox="0 0 24 24" fill="none" stroke="#14aed6" stroke-width="2"><rect x="6" y="2" width="12" height="20" rx="2"/><line x1="11" y1="18" x2="13" y2="18"/></svg>
          (555) 386-7412
        </li>
        <li>
          <svg viewBox="0 0 24 24" fill="none" stroke="#14aed6" stroke-width="2"><rect x="2" y="5" width="20" height="14"/><path d="M2 5l10 8 10-8"/></svg>
          sales@veldmarksupplies.com
        </li>
        <li>
          <svg viewBox="0 0 24 24" fill="none" stroke="#14aed6" stroke-width="2"><circle cx="12" cy="12" r="10"/><path d="M2 12h20M12 2a15 15 0 0 1 0 20M12 2a15 15 0 0 0 0 20"/></svg>
          veldmarksupplies.com
        </li>
      </ul>
    </div>
  </section>

  <section class="card card--back">
    <div class="back__brand">
      <span class="brand-square"></span>
      <span class="brand-name">Veldmark Supplies</span>
    </div>
    <div class="back__info">
      <p class="back__web"><span class="web-blue">www.</span><span class="web-red">veldmarksupplies</span><span class="web-blue">.com</span></p>
      <p class="back__address">418 N.Brantley Suite 6, Midland, Tx 79701</p>
    </div>
  </section>
</main>
</body>
</html>
```